Real Estate Acquisition Company Needs Business Card Design

Bellwick Real Estate is in need of a business card design!

As a Real Estate Acquisition Company, Bellwick Real Estate conducts mutually beneficial real estate transactions that actively consider the needs of the seller. At Bellwick Real Estate we’re actively buying properties from those that see value in a direct transaction, but more importantly want reassurances that they, personally, are in integral part of it. Of course, it all starts with fair market value, but it doesn’t stop there. We’ve found the most success when we offer more. And with our deep experience in this industry, we’ve discovered that we have a lot to offer!

We already have a logo and brand guidelines that we've uploaded. Our final design should stay true to the guidelines. We are looking for a business card design that has two names (Ex. Jane Doe & John Doe) and contact information for each person- this way the company principals can share a card as they often do business as a team.
Updates

The criteria was unfortunately not met on most designs. We are looking for a card that has a layout for TWO names and respective contact information for each of the two people. Almost all designs only had a space for one name and one set of contact information.

Industry/Entity Type

Real Estate

Contact Information for Business Card

We are looking for a business card design that has two names (Ex. Jane Doe & John Doe) and each of their contact information- this way the company principals can share a card as they often do business as a team.

Font styles to use
Other font styles liked:
• Use Brand Guidelines

Requirements
Must have
• Please stay true to our Brand Guidelines for colours, fonts, and positioning of logo.

We require a layout for two names and respective contact information. The company principals work as a team and want a card that has both their information on it.

```html
<!DOCTYPE html>
<html lang="en">
<head>
<meta charset="utf-8">
<title>Bellwick Real Estate – Business Card</title>
<link rel="stylesheet" href="https://fonts.googleapis.com/css2?family=Open+Sans:wght@400;600;700&display=swap">
<style>
  :root {
    --navy: #15213a;
    --gold: #f2b544;
    --white: #ffffff;
    --backdrop: #2e3033;
    --muted: #c9cfdb;
  }
  * { margin: 0; padding: 0; box-sizing: border-box; }
  html, body { width: 1200px; height: 900px; overflow: hidden; }
  body {
    background: var(--backdrop);
    font-family: "Open Sans", Arial, sans-serif;
    position: relative;
  }
  .card {
    position: absolute;
    top: 300px;
    width: 540px;
    height: 300px;
    overflow: hidden;
    border-radius: 3px;
  }
  .card-front { left: 40px; background: var(--navy); }
  .card-back { left: 620px; background: var(--gold); display: flex; align-items: center; justify-content: center; }

  .front-bands { position: absolute; inset: 0; }

  .wordmark {
    position: absolute;
    left: 150px;
    top: 38px;
    width: 360px;
    text-align: center;
    font-weight: 700;
    font-size: 30px;
    letter-spacing: 2px;
    color: var(--navy);
    line-height: 1;
  }
  .card-back .wordmark-back {
    font-weight: 700;
    font-size: 38px;
    letter-spacing: 3px;
    color: var(--white);
  }

  .contact {
    position: absolute;
    color: var(--white);
  }
  .contact-primary { left: 26px; top: 136px; }
  .contact-secondary { left: 296px; top: 186px; }
  .contact-name { font-weight: 700; font-size: 14px; letter-spacing: 1px; }
  .contact-role { font-size: 10px; color: var(--muted); margin-bottom: 8px; }
  .contact-line { display: flex; align-items: center; gap: 8px; font-size: 12px; margin-top: 5px; }
  .contact-line svg { flex: none; }

  .divider {
    position: absolute;
    left: 270px;
    top: 180px;
    width: 1px;
    height: 80px;
    background: linear-gradient(to bottom, transparent, #8a93a6, transparent);
  }

  .address {
    position: absolute;
    left: 26px;
    bottom: 18px;
    color: var(--white);
    font-size: 13px;
  }
</style>
</head>
<body>

<section class="card card-front" aria-label="Card front">
  <svg class="front-bands" width="540" height="300" viewBox="0 0 540 300" aria-hidden="true">
    <polygon points="0,0 540,0 540,170 0,122" fill="#ffffff"/>
    <line x1="0" y1="122" x2="540" y2="170" stroke="#f2b544" stroke-width="2"/>
  </svg>

  <div class="wordmark">BELLWICK REAL ESTATE</div>

  <div class="contact contact-primary">
    <div class="contact-name">JOHN SMITH</div>
    <div class="contact-role">Director and ceo</div>
    <div class="contact-line">
      <svg width="16" height="16" viewBox="0 0 16 16" aria-hidden="true"><rect x="0.5" y="0.5" width="15" height="15" rx="3" fill="none" stroke="#fff"/><path d="M5 4c-1 1-1 3 1 5s4 2 5 1l-1.5-1.5-1 .7C7.5 8.7 7.3 8.5 7 7.5l.7-1L6.2 5z" fill="#fff"/></svg>
      <span>+123 456 7890</span>
    </div>
    <div class="contact-line">
      <svg width="16" height="16" viewBox="0 0 16 16" aria-hidden="true"><rect x="0.5" y="0.5" width="15" height="15" rx="3" fill="none" stroke="#fff"/><rect x="3.5" y="5" width="9" height="6" fill="none" stroke="#fff"/><path d="M3.5 5l4.5 3.5L12.5 5" fill="none" stroke="#fff"/></svg>
      <span>name@website.com</span>
    </div>
  </div>

  <div class="divider"></div>

  <div class="contact contact-secondary">
    <div class="contact-name">JOHN SMITH</div>
    <div class="contact-role">Director and ceo</div>
    <div class="contact-line">
      <svg width="16" height="16" viewBox="0 0 16 16" aria-hidden="true"><rect x="0.5" y="0.5" width="15" height="15" rx="3" fill="none" stroke="#fff"/><path d="M5 4c-1 1-1 3 1 5s4 2 5 1l-1.5-1.5-1 .7C7.5 8.7 7.3 8.5 7 7.5l.7-1L6.2 5z" fill="#fff"/></svg>
      <span>+123 456 7890</span>
    </div>
    <div class="contact-line">
      <svg width="16" height="16" viewBox="0 0 16 16" aria-hidden="true"><rect x="0.5" y="0.5" width="15" height="15" rx="3" fill="none" stroke="#fff"/><rect x="3.5" y="5" width="9" height="6" fill="none" stroke="#fff"/><path d="M3.5 5l4.5 3.5L12.5 5" fill="none" stroke="#fff"/></svg>
      <span>name@website.com</span>
    </div>
  </div>

  <div class="address">#123, Street Name, City Name - 123456</div>
</section>

<section class="card card-back" aria-label="Card back">
  <div class="wordmark-back">BELLWICK REAL ESTATE</div>
</section>

</body>
</html>
```